Brightfield Grove LLC business card

I created a front and back idea of what I want. Also I included my Brightfield Grove logo to be used on the card. Please use your creativity to make it look professional and awesome! Use the all text and phrases in the sample card that I made.

(Front of card)Key words and phrases:
FOOD GROWING MACHINES
Aeroponics Technology
No soil
No pesticides
98% less water
Grow year round

(Back of card)
EVERY MONTH ONE SPIRE PLANTER WILL BE GIVEN AWAY
FOLLOW US ON IG FOR A CHANCE TO WIN A SPIRE PLANTER
FOOD GROWING MACHINES
Vertical Farming
Urban Farming
100% Organic
Grows 40% Faster
Indoors/outdoors

My contact info:
Chef Rolo
Phone:415 637-2094
web: brightfieldgrove.example
IG: brightfieldgrovex

Target Market(s)

urban farming, vertical farming gardening

Industry/Entity Type

Gardening

Contact Information for Business Card

Front of card)Key words and phrases:
FOOD GROWING MACHINES
Aeroponics Technology
No soil
No pesticides
98% less water
Grow year round

(Back of card)
FOOD GROWING MACHINES
Vertical Farming
Urban Farming
100% Organic
Grows 40% Faster
Indoors/outdoors

My contact info:
Phone:415 637-2094
web: brightfieldgrove.example
IG: brightfieldgrovex

Requirements
Must have
• My contact info:
Chef Rolo
Phone:415 637-2094
web: brightfieldgrove.example
IG: brightfieldgrovex
Nice to have
• Great imagery and easy to read. Try to incorporate the image that I uploaded of the little girl.

```html
<!DOCTYPE html>
<html lang="en">
<head>
<meta charset="utf-8">
<title>Brightfield Grove business card</title>
<link rel="stylesheet" href="https://fonts.googleapis.com/css2?family=Archivo:wght@600;700;800;900&display=swap">
<style>
  :root{
    --bg:#e4e4e2;
    --card:#ffffff;
    --green:#2f8f2c;
    --leaf:#6cc04a;
    --pink:#e0356b;
    --ink:#3a3a3a;
    --photo-a:#c9b9a4;
    --photo-b:#8fae6e;
    --photo-c:#d8598f;
  }
  *{box-sizing:border-box;margin:0;padding:0}
  html,body{width:1200px;height:675px;overflow:hidden;background:var(--bg)}
  body{font-family:"Archivo",Arial,sans-serif;position:relative}

  .card{position:absolute;background:var(--card);border-radius:14px;overflow:hidden;box-shadow:0 10px 28px rgba(0,0,0,.18)}

  /* back card (horizontal) */
  .card-back{left:70px;top:178px;width:580px;height:331px}
  .card-back .photo{position:absolute;inset:0;
    background:linear-gradient(110deg,var(--photo-a) 0%,var(--photo-c) 35%,#ddd5c9 50%,var(--photo-b) 75%,#b7cfa0 100%);}
  .card-back .wash{position:absolute;inset:0;background:rgba(255,255,255,.72)}
  .column{position:absolute;top:36px;width:250px;text-align:center}
  .column-left{left:22px}
  .column-right{left:306px;top:78px}
  .column h2{font-weight:900;color:var(--green);font-size:25px;line-height:1.02;letter-spacing:.3px}
  .column h3{font-weight:800;color:var(--ink);font-size:17px;margin-top:3px}
  .features{list-style:none;margin:10px 0 0 38px;text-align:left}
  .features li{display:flex;align-items:center;gap:10px;font-weight:700;color:var(--ink);font-size:15px;height:23px}
  .features svg{width:20px;height:18px;flex:none}
  .divider{position:absolute;left:288px;top:78px;width:4px;height:170px;background:var(--pink)}
  .band{position:absolute;left:0;right:0;bottom:0;height:60px;background:var(--pink);
    display:flex;flex-direction:column;align-items:center;justify-content:center;gap:3px;
    color:#fff;font-weight:800;letter-spacing:.6px}
  .band .giveaway{font-size:16.5px}
  .band .follow{font-size:11.5px;font-weight:700;letter-spacing:.5px}

  /* front card (vertical) */
  .card-front{left:790px;top:48px;width:331px;height:580px}
  .card-front .arc{position:absolute;left:0;top:0;width:331px;height:330px}
  .brand{position:absolute;left:0;right:0;top:345px;text-align:center;
    font-weight:900;color:var(--leaf);font-size:38px;line-height:.95;letter-spacing:.5px;text-transform:uppercase}
  .owner{position:absolute;left:0;right:0;top:440px;text-align:center;
    font-weight:800;color:var(--green);font-size:18px;letter-spacing:.4px}
  .contact{position:absolute;left:60px;top:474px;list-style:none}
  .contact li{display:flex;align-items:center;gap:8px;font-weight:800;color:var(--ink);font-size:16px;height:28px}
  .contact .label{color:var(--pink);font-weight:800;width:18px;display:flex;justify-content:center}
  .contact svg{width:16px;height:16px}
</style>
</head>
<body>

<section class="card card-back" aria-label="Card back">
  <div class="photo" role="img" aria-label="Faded photo of a girl tending leafy greens in a kitchen"></div>
  <div class="wash"></div>

  <div class="column column-left">
    <h2>FOOD GROWING<br>MACHINES</h2>
    <h3>Aeroponics Technology</h3>
    <ul class="features">
      <li><svg viewBox="0 0 20 18"><path d="M2 9l6 6L18 2" fill="none" stroke="#2f8f2c" stroke-width="3.5" stroke-linecap="round" stroke-linejoin="round"/></svg>No soil</li>
      <li><svg viewBox="0 0 20 18"><path d="M2 9l6 6L18 2" fill="none" stroke="#2f8f2c" stroke-width="3.5" stroke-linecap="round" stroke-linejoin="round"/></svg>No pesticides</li>
      <li><svg viewBox="0 0 20 18"><path d="M2 9l6 6L18 2" fill="none" stroke="#2f8f2c" stroke-width="3.5" stroke-linecap="round" stroke-linejoin="round"/></svg>98% less water</li>
      <li><svg viewBox="0 0 20 18"><path d="M2 9l6 6L18 2" fill="none" stroke="#2f8f2c" stroke-width="3.5" stroke-linecap="round" stroke-linejoin="round"/></svg>Grow year round</li>
    </ul>
  </div>

  <div class="divider"></div>

  <div class="column column-right">
    <h2>FOOD GROWING<br>MACHINES</h2>
    <h3>Vertical Farming</h3>
    <ul class="features">
      <li><svg viewBox="0 0 20 18"><path d="M2 9l6 6L18 2" fill="none" stroke="#2f8f2c" stroke-width="3.5" stroke-linecap="round" stroke-linejoin="round"/></svg>Urban Farming</li>
      <li><svg viewBox="0 0 20 18"><path d="M2 9l6 6L18 2" fill="none" stroke="#2f8f2c" stroke-width="3.5" stroke-linecap="round" stroke-linejoin="round"/></svg>100% Organic</li>
      <li><svg viewBox="0 0 20 18"><path d="M2 9l6 6L18 2" fill="none" stroke="#2f8f2c" stroke-width="3.5" stroke-linecap="round" stroke-linejoin="round"/></svg>Grows 40% Faster</li>
      <li><svg viewBox="0 0 20 18"><path d="M2 9l6 6L18 2" fill="none" stroke="#2f8f2c" stroke-width="3.5" stroke-linecap="round" stroke-linejoin="round"/></svg>Indoors/outdoors</li>
    </ul>
  </div>

  <div class="band">
    <span class="giveaway">EVERY MONTH ONE SPIRE PLANTER WILL BE GIVEN AWAY</span>
    <span class="follow">FOLLOW US ON IG FOR A CHANCE TO WIN A SPIRE PLANTER</span>
  </div>
</section>

<section class="card card-front" aria-label="Card front">
  <svg class="arc" viewBox="0 0 331 330" role="img" aria-label="Photo of a girl in a pink shirt rinsing fresh chard in a kitchen">
    <defs>
      <linearGradient id="photo-tones" x1="0" y1="0" x2="1" y2="1">
        <stop offset="0" stop-color="#b7a58f"/>
        <stop offset=".4" stop-color="#d8598f"/>
        <stop offset=".7" stop-color="#9dbb78"/>
        <stop offset="1" stop-color="#5f8f42"/>
      </linearGradient>
    </defs>
    <path d="M0 0H331V120C300 250 170 310 0 300Z" fill="url(#photo-tones)"/>
    <path d="M331 120C300 250 170 310 0 300" fill="none" stroke="#6cc04a" stroke-width="6"/>
    <path d="M331 134C298 262 168 322 0 314" fill="none" stroke="#e0356b" stroke-width="3"/>
  </svg>

  <div class="brand">Brightfield<br>Grove</div>
  <div class="owner">Chef Rolo</div>

  <ul class="contact">
    <li><span class="label"><svg viewBox="0 0 16 16"><path d="M4 1l3 3-2 2c1 2 3 4 5 5l2-2 3 3-2 3C7 15 1 9 1 3z" fill="#e0356b"/></svg></span>: 415 637-2094</li>
    <li><span class="label"><svg viewBox="0 0 16 16"><circle cx="8" cy="8" r="6.5" fill="none" stroke="#e0356b" stroke-width="1.6"/><path d="M1.5 8h13M8 1.5c-3 3.5-3 9.5 0 13M8 1.5c3 3.5 3 9.5 0 13" fill="none" stroke="#e0356b" stroke-width="1.3"/></svg></span>: brightfieldgrove.example</li>
    <li><span class="label">IG</span>: brightfieldgrovex</li>
  </ul>
</section>

</body>
</html>
```